Business card design for my company.
I would like the card's background colour to be black. You can also see our web site to get an idea of our brand. https://www.tmwhomecrafting.com.au/
- Name
- Email

```html
<!DOCTYPE html>
<html lang="en">
<head>
<meta charset="utf-8">
<title>TMW Home Crafting – Business Card</title>
<link rel="stylesheet" href="https://fonts.googleapis.com/css2?family=Roboto:wght@400;500;700&display=swap">
<style>
  :root {
    --stage: #2b2b2b;
    --card: #1c1c1d;
    --card-back: #171718;
    --green: #1f9a47;
    --stripe-grey: #8a8a8a;
    --white: #f4f4f4;
    --muted: #d0d0d0;
    --emboss: #3a3a3c;
  }
  * { margin: 0; padding: 0; box-sizing: border-box; }
  html, body { width: 1200px; height: 852px; overflow: hidden; }
  body {
    background: var(--stage);
    font-family: "Roboto", Arial, sans-serif;
    position: relative;
  }
  .card {
    position: absolute;
    top: 276px;
    width: 525px;
    height: 300px;
    border-radius: 22px;
    overflow: hidden;
  }

  /* Back side */
  .card-back {
    left: 50px;
    background: var(--card-back);
    border-bottom: 9px solid var(--green);
  }
  .card-back .brand-mark {
    position: absolute;
    top: 108px;
    left: 0; right: 0;
    text-align: center;
    font-size: 34px;
    font-weight: 700;
    letter-spacing: 3px;
    color: var(--emboss);
    text-transform: uppercase;
  }
  .card-back .website {
    position: absolute;
    right: 28px;
    bottom: 14px;
    font-size: 13px;
    color: var(--muted);
  }

  /* Front side */
  .card-front {
    left: 625px;
    background: var(--card);
  }
  .card-front .band-green {
    position: absolute;
    left: 0; top: 0; bottom: 0;
    width: 38px;
    background: var(--green);
  }
  .card-front .band-grey {
    position: absolute;
    left: 48px; top: 0; bottom: 0;
    width: 7px;
    background: var(--stripe-grey);
  }
  .card-front .brand-name {
    position: absolute;
    left: 90px;
    top: 58px;
    font-size: 28px;
    font-weight: 700;
    letter-spacing: 2px;
    color: var(--white);
    text-transform: uppercase;
  }
  .card-front .person {
    position: absolute;
    left: 90px;
    top: 142px;
  }
  .person .name {
    font-size: 22px;
    font-weight: 500;
    color: var(--green);
  }
  .person .role {
    font-size: 13px;
    color: var(--white);
    margin-top: 2px;
  }
  .contact {
    position: absolute;
    list-style: none;
    font-size: 12.5px;
    color: var(--muted);
  }
  .contact li {
    display: flex;
    align-items: center;
    gap: 8px;
    margin-bottom: 7px;
  }
  .contact svg { width: 12px; height: 12px; flex: none; fill: var(--green); }
  .contact-left { left: 90px; top: 232px; }
  .contact-right { left: 300px; top: 150px; }
</style>
</head>
<body>

  <section class="card card-back" aria-label="Card back">
    <div class="brand-mark">TMW Home Crafting</div>
    <div class="website">www.tmwhomecrafting.com.au</div>
  </section>

  <section class="card card-front" aria-label="Card front">
    <div class="band-green"></div>
    <div class="band-grey"></div>

    <div class="brand-name">TMW Home Crafting</div>

    <div class="person">
      <div class="name">Dale Morrow</div>
      <div class="role">General Manager</div>
    </div>

    <ul class="contact contact-right">
      <li>
        <svg viewBox="0 0 12 12" aria-hidden="true"><path d="M0 2h12v8H0z M0 2l6 4 6-4" /><path d="M1 3l5 3.4L11 3" stroke="#1c1c1d" stroke-width="1" fill="none"/></svg>
        info@tmwhomecrafting.com.au
      </li>
      <li>
        <svg viewBox="0 0 12 12" aria-hidden="true"><circle cx="6" cy="6" r="6"/><path d="M0 6h12M6 0v12" stroke="#1c1c1d" stroke-width="1"/></svg>
        www.tmwhomecrafting.com.au
      </li>
    </ul>

    <ul class="contact contact-left">
      <li>
        <svg viewBox="0 0 12 12" aria-hidden="true"><path d="M2.5 0.5l2 2.5-1.2 1.5c.8 1.7 2 2.9 3.7 3.7L8.5 7l2.5 2-1 2.5C5 11.3.7 7 .5 2z"/></svg>
        0412 555 018
      </li>
      <li>
        <svg viewBox="0 0 12 12" aria-hidden="true"><path d="M6 0a4 4 0 0 1 4 4c0 3-4 8-4 8S2 7 2 4a4 4 0 0 1 4-4z"/><circle cx="6" cy="4" r="1.5" fill="#1c1c1d"/></svg>
        Devonport, Tasmania, Australia
      </li>
    </ul>
  </section>

</body>
</html>
```